Marrowby Water Taxi and Transport Business Card

I need business cards for my new water taxi and freight transport business I have started here in Kodiak Alaska. Kodiak is a remote island in the middle of the gulf of Alaska. There are seven native villages around the island and Kodiak is the #2 fishing port in the United States. We also have the largest Coast Guard Base in the U.S. My company will be providing water taxi and freight transport logistics to the villages and many hunting and fishing lodges as well as remote properties around the island.

I would like a business card that isn't status quo, something that stands out, either in feel or appearance. I do like clean minimal designs but it needs to have the necessary contact info on it.

Target Market(s)

remote lodge / property owners, residents of the many villages around Kodiak and any one wanting to enjoy the great outdoors of Kodiak Alaska

Industry/Entity Type

Business

Contact Information for Business Card

I like clean simple designs that aren't cluttered but still provide the necessary information

Colors
0255a3
3277b5
33a4d5
9bcb3c
add136
fbed22
ffc214
f78f20
f37122

Requirements
Must have
• logo and contact info
• Captain Mason Elwick
• www.marrowbyferryline.com
• mason@marrowbyferryline.com

```html
<!DOCTYPE html>
<html lang="en">
<head>
<meta charset="utf-8">
<title>Marrowby Water Taxi and Transport – Business Card</title>
<link rel="stylesheet" href="https://fonts.googleapis.com/css2?family=Montserrat:wght@500;700&family=Open+Sans:wght@400&display=swap">
<style>
  :root {
    --navy: #0255a3;
    --mid-blue: #3277b5;
    --sky: #33a4d5;
    --orange: #f78f20;
    --ink: #555a60;
    --rule: #c9cdd2;
    --paper: #ffffff;
    --backdrop: #e9e6e1;
  }
  * { box-sizing: border-box; margin: 0; padding: 0; }
  html, body { width: 1200px; height: 950px; overflow: hidden; }
  body {
    background: var(--backdrop);
    font-family: "Open Sans", Arial, sans-serif;
    position: relative;
  }
  .card {
    position: absolute;
    left: 320px;
    width: 560px;
    height: 320px;
    background: var(--paper);
    box-shadow: 0 6px 18px rgba(0,0,0,0.18);
  }
  .card--front { top: 130px; }
  .card--back  { top: 500px; }

  /* front */
  .front-logo {
    position: absolute;
    left: 52px; top: 48px;
    width: 150px; height: 112px;
  }
  .identity {
    position: absolute;
    left: 222px; top: 76px;
  }
  .identity__name {
    font-family: "Montserrat", Arial, sans-serif;
    font-weight: 700;
    font-size: 30px;
    letter-spacing: 0.5px;
    color: var(--navy);
    text-transform: uppercase;
  }
  .identity__role {
    font-family: "Montserrat", Arial, sans-serif;
    font-weight: 500;
    font-size: 18px;
    color: var(--orange);
    margin-top: 2px;
    padding-left: 64px;
  }
  .front-rule {
    position: absolute;
    left: 52px; top: 182px;
    width: 420px; height: 1px;
    background: var(--rule);
  }
  .contact {
    position: absolute;
    left: 52px; top: 200px;
    font-size: 14.5px;
    line-height: 24px;
    color: var(--ink);
    list-style: none;
  }
  .contact .sep { color: var(--rule); padding: 0 6px; }

  /* back */
  .social {
    position: absolute;
    left: 40px; top: 122px;
    display: flex;
    flex-direction: column;
    gap: 10px;
  }
  .social__dot {
    width: 22px; height: 22px;
    border-radius: 50%;
    background: var(--mid-blue);
  }
  .back-rule {
    position: absolute;
    left: 86px; top: 70px;
    width: 1px; height: 180px;
    background: var(--rule);
  }
  .back-logo {
    position: absolute;
    left: 340px; top: 40px;
    width: 150px; height: 112px;
  }
  .brand {
    position: absolute;
    left: 170px; top: 172px;
  }
  .brand__name {
    font-family: "Montserrat", Arial, sans-serif;
    font-weight: 700;
    font-size: 46px;
    letter-spacing: 1px;
    color: var(--navy);
    text-transform: uppercase;
    line-height: 1;
  }
  .brand__tagline {
    font-family: "Montserrat", Arial, sans-serif;
    font-weight: 500;
    font-size: 17px;
    color: var(--mid-blue);
    margin-top: 8px;
  }
</style>
</head>
<body>

<section class="card card--front" aria-label="Business card front">
  <svg class="front-logo" viewBox="0 0 150 112" role="img" aria-label="Company emblem: boat before icy mountains with a rising sun">
    <defs>
      <linearGradient id="emblemFront" x1="0" y1="0" x2="1" y2="1">
        <stop offset="0" stop-color="#f78f20"/>
        <stop offset="0.35" stop-color="#33a4d5"/>
        <stop offset="1" stop-color="#3277b5"/>
      </linearGradient>
    </defs>
    <rect width="150" height="112" rx="8" fill="url(#emblemFront)" opacity="0.85"/>
  </svg>

  <div class="identity">
    <h1 class="identity__name">Mason Elwick</h1>
    <p class="identity__role">Captain</p>
  </div>

  <div class="front-rule"></div>

  <ul class="contact">
    <li>4120 Harbor View Road, Marrowby, Alaska 99615</li>
    <li>555 014 2290<span class="sep">|</span>mason@marrowbyferryline.com</li>
    <li>www.marrowbyferryline.com</li>
  </ul>
</section>

<section class="card card--back" aria-label="Business card back">
  <div class="social" aria-label="Social links">
    <span class="social__dot"></span>
    <span class="social__dot"></span>
    <span class="social__dot"></span>
  </div>
  <div class="back-rule"></div>

  <svg class="back-logo" viewBox="0 0 150 112" role="img" aria-label="Company emblem: boat before icy mountains with a rising sun">
    <defs>
      <linearGradient id="emblemBack" x1="1" y1="0" x2="0" y2="1">
        <stop offset="0" stop-color="#f78f20"/>
        <stop offset="0.35" stop-color="#33a4d5"/>
        <stop offset="1" stop-color="#3277b5"/>
      </linearGradient>
    </defs>
    <rect width="150" height="112" rx="8" fill="url(#emblemBack)" opacity="0.85"/>
  </svg>

  <div class="brand">
    <p class="brand__name">Marrowby</p>
    <p class="brand__tagline">Water Taxi &amp; Transport</p>
  </div>
</section>

</body>
</html>
```